Meridale Bed Company Needs Business Card

Looking for a very nice looking business card. Creative but not extravagant. We sell beds and pillows across the U.S. and need something professional but catchy. I have attached the logo.

Name : Devin Holt
Title : President
Phone : (800) 471-2960
Email: sleep@quilmora.com
Website: www.quilmora.com

Can be single-sided or double-sided
horizontal or vertical

Can use Blues/Greys

Target Market(s)

Mass Market

Industry/Entity Type

Retail

Contact Information for Business Card

Name : Devin Holt
Title : President
Phone : (800) 471-2960
Email: sleep@quilmora.com
Website: www.quilmora.com

Requirements
Must have
• Clean, Modern, Smooth
• Can use Blues/Greys
• On the other side without the information - have something simple like www.quilmora.com or our logo
Nice to have
• Surprise me
Should not have
• Nothing crazy, nothing cluttered

```html
<!DOCTYPE html>
<html lang="en">
<head>
<meta charset="utf-8">
<title>Meridale Bed Company – Business Card</title>
<link href="https://fonts.googleapis.com/css2?family=Arimo:wght@400;700&display=swap" rel="stylesheet">
<style>
  :root {
    --backdrop: #2a2a2c;
    --card-white: #ffffff;
    --card-grey: #5b5b5d;
    --brand-blue: #35b1e0;
    --ink-grey: #8a8a8c;
    --on-grey: #ffffff;
  }
  * { margin: 0; padding: 0; box-sizing: border-box; }
  html, body {
    width: 1200px; height: 795px; overflow: hidden;
    background: var(--backdrop);
    font-family: "Arimo", sans-serif;
  }
  .stage {
    width: 1200px; height: 795px;
    display: flex; align-items: center; justify-content: center; gap: 70px;
  }
  .card {
    position: relative;
    width: 320px; height: 560px;
    overflow: hidden;
  }
  .card--front { background: var(--card-white); }
  .card--back { background: var(--card-grey); }

  .name-band { position: absolute; top: 30px; left: 0; width: 320px; height: 86px; }
  .name-band svg { display: block; }
  .holder {
    position: absolute; top: 48px; left: 46px; color: #fff;
  }
  .holder__name { font-size: 19px; font-weight: 700; line-height: 1.1; }
  .holder__title { font-size: 14px; font-weight: 400; }

  .brand-name {
    font-family: "Arimo", sans-serif;
    font-weight: 400; white-space: nowrap; line-height: 1;
  }
  .card--front .brand-name {
    position: absolute; top: 318px; right: 28px;
    font-size: 52px; color: var(--brand-blue);
  }

  .contact {
    position: absolute; right: 28px; bottom: 52px;
    list-style: none; text-align: right;
    font-size: 13px; color: var(--ink-grey); line-height: 21px;
  }
  .contact li { display: flex; align-items: center; justify-content: flex-end; gap: 8px; }
  .contact svg { width: 12px; height: 12px; flex: none; }

  .card--back .brand-name {
    position: absolute; left: 175px; top: 50%;
    transform: translate(-50%, -50%) rotate(90deg);
    font-size: 72px; color: var(--on-grey);
  }
  .back-url {
    position: absolute; left: 108px; top: 50%;
    transform: translate(-50%, -50%) rotate(90deg);
    font-size: 11px; letter-spacing: 5px; color: var(--on-grey); white-space: nowrap;
  }
</style>
</head>
<body>
<main class="stage">
  <section class="card card--front" aria-label="Card front">
    <div class="name-band">
      <svg width="320" height="86" viewBox="0 0 320 86">
        <polygon points="0,0 255,0 292,60 268,86 0,86" fill="var(--brand-blue)"/>
      </svg>
    </div>
    <div class="holder">
      <p class="holder__name">Devin Holt</p>
      <p class="holder__title">President</p>
    </div>
    <p class="brand-name">quilmora</p>
    <ul class="contact">
      <li>(800) 471-2960
        <svg viewBox="0 0 12 12"><path d="M1 4c0-2 3-2 5-2s5 0 5 2v1H8V4H4v1H1z M3 6h6l1 5H2z" fill="var(--brand-blue)"/></svg>
      </li>
      <li>sleep@quilmora.com
        <svg viewBox="0 0 12 12"><rect x="0.5" y="2.5" width="11" height="7" fill="var(--brand-blue)"/><path d="M0.5 2.5 6 7 11.5 2.5" fill="none" stroke="#fff" stroke-width="1"/></svg>
      </li>
      <li>www.quilmora.com
        <svg viewBox="0 0 12 12"><circle cx="6" cy="6" r="5.5" fill="var(--brand-blue)"/><path d="M1 6h10M6 1c-2.5 3-2.5 7 0 10M6 1c2.5 3 2.5 7 0 10" fill="none" stroke="#fff" stroke-width="0.8"/></svg>
      </li>
    </ul>
  </section>

  <section class="card card--back" aria-label="Card back">
    <p class="brand-name">quilmora</p>
    <p class="back-url">quilmora.com</p>
  </section>
</main>
</body>
</html>
```